Software Development Consulting Company Needs Business Card Design

We need a new business card design for our consultants at Kestrel Works (kestrelworks.example). We are a small firm that provides high-end software development and methodology consulting to medium to large enterprise IT organizations.

Our logo uses Futura for the font and we would like to stick with navy blue and canary yellow for the logo colors. Attached are normal and reversed versions of our logos in illustrator format.
Updates

Hi Everyone, Thank yo very much for your amazing design ideas. I have created a poll for this project and our employees will be voting on the design they wish to use. We will be making a decision this Wednesday (October 22nd). Thanks again, Dale Hartwick

Industry/Entity Type

Business

```html
<!DOCTYPE html>
<html lang="en">
<head>
<meta charset="utf-8">
<title>Kestrel Works – Business Card</title>
<link rel="stylesheet" href="https://fonts.googleapis.com/css2?family=Jost:wght@400;500;600&display=swap">
<style>
  :root {
    --navy: #1b4a73;
    --canary: #ffef00;
    --canary-line: #f2e21a;
    --paper: #ffffff;
    --ink-grey: #55565a;
    --rule-grey: #c9cacc;
    --backdrop: #ecebe8;
  }
  * { box-sizing: border-box; margin: 0; padding: 0; }
  html, body {
    width: 1200px; height: 720px; overflow: hidden;
    background: var(--backdrop);
    font-family: "Jost", "Futura", sans-serif;
  }
  .stage {
    width: 1200px; height: 720px;
    display: flex; align-items: center; justify-content: center; gap: 60px;
  }
  .card {
    position: relative;
    width: 520px; height: 297px;
    box-shadow: 0 6px 18px rgba(0,0,0,0.18);
    overflow: hidden;
  }

  /* Front */
  .card-front { background: var(--paper); }
  .accent-line {
    position: absolute; left: 0; right: 0; height: 2px;
    background: var(--canary-line);
  }
  .accent-line.upper { top: 52px; }
  .accent-line.lower { top: 104px; }
  .name-band {
    position: absolute; left: 0; right: 0; top: 58px; height: 40px;
    background: var(--navy);
    display: flex; align-items: center; justify-content: flex-end;
    padding-right: 150px;
    color: var(--paper);
    font-size: 15px; letter-spacing: 0.3px;
  }
  .name-band .person-name { font-weight: 600; }
  .name-band .person-title { font-weight: 400; margin-left: 4px; }

  .brand {
    position: absolute;
    display: flex; align-items: center;
    color: var(--navy);
    font-weight: 500;
    text-transform: uppercase;
    white-space: nowrap;
  }
  .brand-dot {
    flex: none;
    border-radius: 50%;
    border: 3px solid var(--navy);
  }
  .card-front .brand {
    left: 30px; top: 180px; width: 270px;
    gap: 8px;
    font-size: 21px; letter-spacing: 2px;
  }
  .card-front .brand-dot { width: 22px; height: 22px; border-width: 2.5px; }

  .divider {
    position: absolute; left: 318px; top: 124px; width: 1px; height: 140px;
    background: linear-gradient(var(--paper), var(--rule-grey) 30%, var(--rule-grey) 70%, var(--paper));
  }
  .contact-list {
    position: absolute; left: 336px; top: 140px;
    list-style: none;
    color: var(--ink-grey);
    font-size: 12.5px; line-height: 22px;
  }
  .contact-list li { display: flex; align-items: center; gap: 6px; }
  .contact-icon { width: 13px; height: 13px; flex: none; }

  /* Back */
  .card-back { background: var(--canary); }
  .card-back .brand {
    left: 0; right: 0; top: 100px; justify-content: center;
    gap: 10px;
    font-size: 36px; letter-spacing: 4px;
  }
  .card-back .brand-dot { width: 32px; height: 32px; }
  .back-url {
    position: absolute; left: 0; right: 0; top: 232px;
    text-align: center;
    color: var(--ink-grey);
    font-size: 15px; letter-spacing: 2.5px;
  }
</style>
</head>
<body>
<main class="stage">

  <section class="card card-front" aria-label="Business card front">
    <div class="accent-line upper"></div>
    <div class="name-band">
      <span class="person-name">YOUR NAME,</span><span class="person-title">TITLE</span>
    </div>
    <div class="accent-line lower"></div>

    <div class="brand">
      <span class="brand-dot"></span>
      <span class="brand-name">Kestrel Works</span>
    </div>

    <div class="divider"></div>

    <ul class="contact-list">
      <li>
        <svg class="contact-icon" viewBox="0 0 14 14" aria-hidden="true">
          <circle cx="7" cy="7" r="7" fill="var(--ink-grey)"/>
          <path d="M4.6 3.6l1.3 0 .6 1.7-.8.6c.4.9 1.1 1.6 2 2l.6-.8 1.7.6 0 1.3c-3 .3-5.7-2.4-5.4-5.4z" fill="#fff"/>
        </svg>
        012-555-0147
      </li>
      <li>
        <svg class="contact-icon" viewBox="0 0 14 14" aria-hidden="true">
          <circle cx="7" cy="7" r="7" fill="var(--ink-grey)"/>
          <rect x="3.5" y="4.5" width="7" height="5" fill="#fff"/>
          <path d="M3.5 4.7l3.5 2.6 3.5-2.6" stroke="var(--ink-grey)" stroke-width="0.8" fill="none"/>
        </svg>
        info@kestrelworks.example
      </li>
      <li>
        <svg class="contact-icon" viewBox="0 0 14 14" aria-hidden="true">
          <circle cx="7" cy="7" r="7" fill="var(--ink-grey)"/>
          <circle cx="7" cy="7" r="3.6" stroke="#fff" stroke-width="0.9" fill="none"/>
          <path d="M3.4 7h7.2M7 3.4v7.2" stroke="#fff" stroke-width="0.8"/>
        </svg>
        www.kestrelworks.example
      </li>
      <li class="location">Denver + Boulder, CO</li>
    </ul>
  </section>

  <section class="card card-back" aria-label="Business card back">
    <div class="brand">
      <span class="brand-dot"></span>
      <span class="brand-name">Kestrel Works</span>
    </div>
    <p class="back-url">www.kestrelworks.example</p>
  </section>

</main>
</body>
</html>
```